Professional Website for Leading Global Private Equity Real Estate Company

The company is a leading global Private Equity Real Estate (PERE). We need a homepage design, an inner page design, and color/font tweaks to the logo (color should be more soothing than current blue used in the logo). The logo website should project the company as global, professional, experienced, trustworthy, accessible, YOUNG, DYNAMIC, hi-tech. PLEASE SEE the attached Design Brief Word Doc for details.

Target Market(s)

institional investors and wealthy private individuals

Industry/Entity Type

Finance

Number of Pages Required

2 page

Font styles to use
Sans Serif
Other font styles liked:
• either like in https://www.ferndalequay.com/ or like in presentations (Montserrat Black & Montserrat Light, Century Gothic, Blair ITC, Almoni Neue DL 4.0 AAA Medium, Almoni DL AAA)

Requirements
Must have
• new color palette that is NOT based on current logo. they want a more soothing color palette than the blue in that logo. the new color palette should project: global, professional, experienced, trustworthy, accessible, YOUNG, DYNAMIC, hi-tech.
Nice to have
• the likes these sites: https://www.ferndalequay.com/ and https://www.tvr.law/

```html
<!DOCTYPE html>
<html lang="en">
<head>
<meta charset="utf-8">
<title>Vantora Real Estate</title>
<link href="https://fonts.googleapis.com/css2?family=Montserrat:wght@300;400;500;600;700;800&display=swap" rel="stylesheet">
<style>
:root{
  --gold:#c9a445;
  --gold-dark:#a8862f;
  --ink:#1c1c1c;
  --charcoal:#262626;
  --muted:#6b6b6b;
  --light:#f4f3f0;
  --white:#ffffff;
}
*{box-sizing:border-box;margin:0;padding:0}
html,body{width:1200px;height:4084px;overflow:hidden}
body{font-family:'Montserrat',sans-serif;color:var(--ink);background:var(--white);position:relative}
section,header,footer{position:absolute;left:0;width:1200px}
.btn{display:inline-flex;align-items:center;gap:10px;background:var(--gold);color:var(--white);border-radius:30px;padding:6px 22px 6px 6px;font-size:13px;font-weight:600}
.btn i{width:28px;height:28px;border-radius:50%;background:var(--white);display:flex;align-items:center;justify-content:center}
.btn i svg{width:12px;height:12px}
.h2{font-size:40px;font-weight:700}
.h2 span{color:var(--gold)}
.copy{font-size:13px;line-height:1.75;color:var(--muted)}
.photo{position:absolute}

/* top bar */
.topbar{top:0;height:72px;background:var(--ink);display:flex;align-items:center;justify-content:space-between;padding:0 160px;color:var(--white);font-size:13px}
.topbar .item{display:flex;align-items:center;gap:10px}
.dot{width:26px;height:26px;border-radius:50%;background:var(--gold);display:inline-block}
.brand{font-weight:800;letter-spacing:4px;font-size:26px;color:var(--white);display:flex;align-items:center;gap:10px}
.brand .sq{width:18px;height:18px;background:var(--gold)}
.nav{top:72px;height:56px;background:var(--gold);display:flex;align-items:center;justify-content:space-between;padding:0 160px;color:var(--white);font-size:14px;font-weight:500}

/* hero */
.hero{top:128px;height:624px;background:linear-gradient(180deg,#6f7d8c 0%,#9aa9b6 45%,#b9c2c9 100%)}
.hero .title{position:absolute;top:170px;width:100%;text-align:center;color:var(--white);font-size:48px;font-weight:700;line-height:1.25}
.hero .btn{position:absolute;top:310px;left:532px}

/* about */
.about{top:752px;height:538px;background:var(--light);text-align:center}
.about .h2{margin-top:64px}
.about .copy{width:720px;margin:22px auto 0}
.about .btn{margin-top:24px}
.stats{display:flex;justify-content:center;gap:40px;margin-top:44px}
.stat{width:170px;text-align:left}
.stat b{display:block;font-size:34px;font-weight:700;color:var(--gold)}
.stat em{font-style:normal;font-size:18px;color:var(--gold);font-weight:500}
.stat .card{margin-top:10px;background:var(--white);height:100px;box-shadow:0 4px 16px rgba(0,0,0,.08);display:flex;flex-direction:column;align-items:center;justify-content:center;gap:10px;font-size:12px;font-weight:600}
.stat .card svg{width:26px;height:26px}

/* platforms */
.platforms{top:1290px;height:710px;background:var(--white)}
.platforms .h2{text-align:center;margin-top:50px}
.platforms .dark{position:absolute;top:250px;left:0;width:1200px;height:460px;background:linear-gradient(135deg,#2a2a2a,#1a1a1a)}
.tabs{position:absolute;top:158px;left:168px;display:flex;gap:16px}
.tab{width:160px;height:172px;background:var(--ink);border-radius:8px;color:var(--white);display:flex;flex-direction:column;align-items:center;justify-content:center;gap:8px;font-weight:800;letter-spacing:2px;font-size:18px}
.tab small{font-size:10px;letter-spacing:1px;font-weight:500;color:var(--gold)}
.tab.active{background:var(--gold);transform:translateY(-14px)}
.tab.active small{color:var(--white)}
.platforms .photo{top:370px;left:160px;width:420px;height:280px;background:linear-gradient(135deg,#d9dde0,#8f969c);border-radius:8px}
.platforms .text{position:absolute;top:380px;left:628px;width:440px;color:#d0d0d0}
.platforms .text h3{color:var(--white);font-size:22px;font-weight:600;margin-bottom:14px}
.platforms .text p{font-size:13px;line-height:1.7;margin-bottom:12px}

/* edge */
.edge{top:2000px;height:440px;background:var(--white)}
.edge .text{position:absolute;top:70px;left:160px;width:400px}
.edge .copy{margin:18px 0 22px}
.edge .photo{top:20px;left:600px;width:600px;height:420px;background:linear-gradient(135deg,#c9d2d6,#6c7a80)}

/* newsletter */
.news{top:2440px;height:300px;background:var(--charcoal);text-align:center;color:var(--white)}
.news .h2{margin-top:70px}
.news p{font-size:13px;color:#bdbdbd;margin-top:14px}
.field{width:420px;height:40px;margin:22px auto 0;background:var(--white);border-radius:24px;display:flex;align-items:center;justify-content:space-between;padding:0 4px 0 20px;font-size:12px;color:#999}
.field i{width:32px;height:32px;border-radius:50%;background:var(--gold);display:flex;align-items:center;justify-content:center}

/* responsibility */
.resp{top:2740px;height:420px;background:var(--white)}
.resp .photo{top:0;left:0;width:600px;height:420px;background:linear-gradient(135deg,#8a9096,#c8cdd0)}
.resp .text{position:absolute;top:70px;left:628px;width:420px}
.resp .copy{margin:18px 0 22px}

/* enquiry */
.enquiry{top:3160px;height:560px;background:linear-gradient(180deg,#3b2e26,#21201f)}
.enquiry .inner{position:absolute;top:60px;width:100%;text-align:center;color:var(--white)}
.enquiry p{font-size:13px;color:#d6d6d6;width:620px;margin:14px auto 0;line-height:1.6}
.form{width:600px;margin:24px auto 0;display:grid;grid-template-columns:1fr 1fr;gap:12px}
.form div{height:34px;border:1px solid rgba(255,255,255,.4);background:rgba(255,255,255,.08);text-align:left;padding:9px 12px;font-size:11px;color:#ddd}
.form .msg{grid-column:1/3;height:90px}
.enquiry .btn{margin-top:28px}

/* footer */
.footer{top:3720px;height:320px;background:var(--white);padding:50px 160px 0;display:grid;grid-template-columns:1.4fr 1fr 1.1fr 1.3fr;gap:30px}
.footer .brand{color:var(--ink);font-size:24px}
.footer h4{color:var(--gold);font-size:16px;font-weight:600;margin-bottom:14px}
.footer li{list-style:none;font-size:12px;color:var(--muted);line-height:2}
.footer .copy{font-size:12px;margin-top:16px}
.contact{display:flex;gap:10px;margin-bottom:14px;font-size:12px;color:var(--muted)}
.contact b{display:block;color:var(--ink);font-weight:600}
.contact .dot{width:22px;height:22px;flex:none}
.bottom{top:4040px;height:44px;background:var(--gold);color:var(--white);display:flex;align-items:center;justify-content:space-between;padding:0 160px;font-size:12px}
.bottom .soc{display:flex;gap:14px}
.bottom .soc span{width:14px;height:14px;border-radius:50%;background:var(--white)}
</style>
</head>
<body>

<header class="topbar">
  <div class="item"><span class="dot"></span>info@vantora.com</div>
  <div class="brand"><span class="sq"></span>VANTORA</div>
  <div class="item"><span class="dot"></span>Login</div>
</header>
<nav class="nav header" style="position:absolute;left:0;width:1200px">
  <span>Home</span><span>About Us</span><span>Our Businesses</span><span>Investors</span><span>News</span><span>Contact Us</span>
</nav>

<section class="hero" role="img" aria-label="Upward view of glass office towers against the sky">
  <div class="title">We are leading global Private<br>Equity Real Estate Firm</div>
  <span class="btn"><i><svg viewBox="0 0 12 12"><path d="M2 6h8M7 3l3 3-3 3" stroke="#c9a445" stroke-width="1.6" fill="none"/></svg></i>About Us</span>
</section>

<section class="about">
  <div class="h2">About <span>Us</span></div>
  <p class="copy">Vantora Holdings is part of a wider group and was founded many years ago as a leading importer and manufacturer of home appliances and climate systems. The group is engaged in the production, import, sales, distribution, marketing and provision of services for a broad variety of consumer appliances. The company has an annual sales turnover of several billion and employs around 1,400 people.</p>
  <span class="btn"><i><svg viewBox="0 0 12 12"><path d="M2 6h8M7 3l3 3-3 3" stroke="#c9a445" stroke-width="1.6" fill="none"/></svg></i>Read More</span>
  <div class="stats">
    <div class="stat"><b>4.6</b><em>NIS Billion</em><div class="card"><svg viewBox="0 0 26 26"><rect x="3" y="14" width="4" height="9" fill="#c9a445"/><rect x="11" y="9" width="4" height="14" fill="#c9a445"/><rect x="19" y="4" width="4" height="19" fill="#c9a445"/></svg>Annual Revenues</div></div>
    <div class="stat"><b>265.59</b><em>NIS Million</em><div class="card"><svg viewBox="0 0 26 26"><circle cx="13" cy="13" r="10" stroke="#c9a445" stroke-width="2" fill="none"/><path d="M13 7v12M9 10h6a2 2 0 010 4h-4a2 2 0 000 4h6" stroke="#c9a445" stroke-width="1.6" fill="none"/></svg>Annual Operating Income</div></div>
    <div class="stat"><b>164</b><em>NIS Million</em><div class="card"><svg viewBox="0 0 26 26"><path d="M3 20l7-7 5 4 8-10" stroke="#c9a445" stroke-width="2" fill="none"/></svg>Annual Net Profit</div></div>
    <div class="stat"><b>1.2</b><em>NIS Billion</em><div class="card"><svg viewBox="0 0 26 26"><path d="M13 3v10h10A10 10 0 1113 3z" fill="#c9a445"/></svg>Equity</div></div>
  </div>
</section>

<section class="platforms">
  <div class="h2">Our Investment <span>Platforms</span></div>
  <div class="dark"></div>
  <div class="tabs">
    <div class="tab">VANTORA<small>MULTIFAMILY</small></div>
    <div class="tab active">VANTORA<small>DEBT</small></div>
    <div class="tab">VANTORA<small>SINGLE FAMILY</small></div>
    <div class="tab">VANTORA<small>HOSPITALITY</small></div>
    <div class="tab">VANTORA<small>UK</small></div>
  </div>
  <div class="photo" role="img" aria-label="Business people reviewing documents at a laptop"></div>
  <div class="text">
    <h3>Vantora Debt</h3>
    <p>Lorem ipsum dolor sit amet, consectetuer adipiscing elit, sed diam nonummy nibh euismod tincidunt ut laoreet dolore magna aliquam erat volutpat.</p>
    <p>Lorem ipsum dolor sit amet, consectetuer adipiscing elit, sed diam nonummy.</p>
    <p>Lorem ipsum dolor sit amet, consectetuer adipiscing elit, sed diam nonummy.</p>
    <span class="btn"><i><svg viewBox="0 0 12 12"><path d="M2 6h8M7 3l3 3-3 3" stroke="#c9a445" stroke-width="1.6" fill="none"/></svg></i>Contact Us</span>
  </div>
</section>

<section class="edge">
  <div class="text">
    <div class="h2">Our <span>Edge</span></div>
    <p class="copy">Lorem ipsum dolor sit amet, consectetuer adipiscing elit, sed diam nonummy nibh euismod tincidunt ut laoreet dolore magna aliquam erat volutpat. Lorem ipsum dolor sit amet, consectetuer adipiscing elit, sed diam nonummy. Lorem ipsum dolor sit amet, consectetuer adipiscing elit, sed diam nonummy.</p>
    <span class="btn"><i><svg viewBox="0 0 12 12"><path d="M2 6h8M7 3l3 3-3 3" stroke="#c9a445" stroke-width="1.6" fill="none"/></svg></i>Investor Information</span>
  </div>
  <div class="photo" role="img" aria-label="Two businessmen in suits talking on a sofa in a bright office"></div>
</section>

<section class="news">
  <div class="h2">Newsletter <span>Signup</span></div>
  <p>Lorem ipsum dolor sit amet, consectetuer adipiscing elit, sed diam nonummy.</p>
  <div class="field">Enter email<i><svg viewBox="0 0 12 12" width="12" height="12"><path d="M2 6h8M7 3l3 3-3 3" stroke="#fff" stroke-width="1.6" fill="none"/></svg></i></div>
</section>

<section class="resp">
  <div class="photo" role="img" aria-label="Two businessmen reviewing papers in a city-view office"></div>
  <div class="text">
    <div class="h2">Our <span>Responsibility</span></div>
    <p class="copy">Lorem ipsum dolor sit amet, consectetuer adipiscing elit, sed diam nonummy nibh euismod tincidunt ut laoreet dolore magna aliquam erat volutpat. Lorem ipsum dolor sit amet, consectetuer adipiscing elit, sed diam nonummy.</p>
    <span class="btn"><i><svg viewBox="0 0 12 12"><path d="M2 6h8M7 3l3 3-3 3" stroke="#c9a445" stroke-width="1.6" fill="none"/></svg></i>Read More</span>
  </div>
</section>

<section class="enquiry" role="img" aria-label="Business meeting around a table with a brick wall behind">
  <div class="inner">
    <div class="h2">Quick Enquiry</div>
    <p>Lorem ipsum dolor sit amet, consectetuer adipiscing elit, sed diam nonummy nibh euismod tincidunt ut laoreet dolore magna aliquam erat volutpat, sed diam nonummy nibh.</p>
    <div class="form">
      <div>Name</div><div>Email</div><div>Phone</div><div>Company</div><div class="msg">Message</div>
    </div>
    <span class="btn"><i><svg viewBox="0 0 12 12"><path d="M2 6h8M7 3l3 3-3 3" stroke="#c9a445" stroke-width="1.6" fill="none"/></svg></i>Get in Touch</span>
  </div>
</section>

<footer class="footer">
  <div>
    <div class="brand"><span class="sq"></span>VANTORA</div>
    <p class="copy">Lorem ipsum dolor sit amet, consectetuer adipiscing elit, sed diam nonummy nibh euismod tincidunt ut laoreet dolore magna aliquam erat volutpat.</p>
  </div>
  <div><h4>Quick Links</h4><ul><li>Home</li><li>About Us</li><li>Our Businesses</li><li>Investors</li><li>News</li><li>Contact Us</li></ul></div>
  <div><h4>Our Businesses</h4><ul><li>Vantora Multifamily</li><li>Vantora Debt</li><li>Vantora Single Family</li><li>Vantora Hospitality</li><li>Vantora UK</li></ul></div>
  <div><h4>Contact Details</h4>
    <div class="contact"><span class="dot"></span><div><b>Address</b>Street Name, City - 000 000</div></div>
    <div class="contact"><span class="dot"></span><div><b>Phone</b>+000 000 0000</div></div>
    <div class="contact"><span class="dot"></span><div><b>Email</b>info@vantora.com</div></div>
  </div>
</footer>
<div class="bottom" style="position:absolute;left:0;width:1200px">
  <span>Copyright © 2022 Vantora. All Rights Reserved.</span>
  <div class="soc"><span></span><span></span><span></span></div>
</div>

</body>
</html>
```